Local fast-growing company in the service sector

We are looking for a modern business card design, which should also appear on our letterheads

Target Market(s)

Private and industrial sectors

Contact Information for Business Card

Vorname Name
Kellberger Str. 18
73614 Schorndorf
Tel.: 07146-839214-0
Name@agentur-kvtl.de

Colors
9d9d9d
919191
aaaaaa

Requirements
Must have
• The logo (file) in silver

```html
<!DOCTYPE html>
<html lang="de">
<head>
<meta charset="utf-8">
<title>KVTL Visitenkarte</title>
<link href="https://fonts.googleapis.com/css2?family=Roboto:wght@400;500;700&display=swap" rel="stylesheet">
<style>
  :root {
    --page-bg: #e6e3df;
    --card-dark: #1b1c1e;
    --card-light: #f4f4f4;
    --silver: #aaaaaa;
    --silver-mid: #9d9d9d;
    --silver-deep: #919191;
    --silver-light: #d6d6d6;
    --white: #ffffff;
    --card-shadow: 0 6px 14px rgba(0,0,0,.35);
  }
  * { box-sizing: border-box; margin: 0; padding: 0; }
  html, body { width: 1200px; height: 960px; overflow: hidden; }
  body {
    position: relative;
    background: var(--page-bg);
    font-family: "Roboto", Arial, sans-serif;
  }
  .card {
    position: absolute;
    border-radius: 18px;
    overflow: hidden;
    box-shadow: var(--card-shadow);
  }
  /* Front */
  .card-front {
    left: 320px; top: 100px; width: 610px; height: 350px;
    background: var(--card-dark);
  }
  .front-wordmark {
    position: absolute; left: 36px; top: 210px;
    font-weight: 700; font-size: 66px; line-height: 1;
    letter-spacing: 2px; color: var(--silver);
  }
  .front-url {
    position: absolute; left: 36px; top: 304px;
    font-size: 15px; letter-spacing: 3.2px; color: var(--white);
  }
  .front-mark {
    position: absolute; left: 310px; top: 30px;
    width: 250px; height: 250px; border-radius: 14px;
    background: linear-gradient(135deg, var(--silver-light), var(--silver-mid));
  }
  /* Back */
  .card-back {
    left: 320px; top: 493px; width: 600px; height: 342px;
    background: var(--card-light);
  }
  .back-logo {
    position: absolute; right: 24px; top: 42px;
    display: flex; align-items: center; gap: 12px;
  }
  .back-logo-square {
    width: 50px; height: 50px; border-radius: 4px;
    background: var(--silver);
  }
  .back-wordmark {
    font-weight: 700; font-size: 42px; line-height: 1;
    letter-spacing: 1px; color: var(--silver-deep);
  }
  .contact-band {
    position: absolute; left: 0; top: 131px; width: 100%; height: 211px;
    background: radial-gradient(ellipse at 25% 40%, #c9c9c9 0%, var(--silver-mid) 55%, #7c7c7c 100%);
  }
  .person-name {
    position: absolute; left: 35px; top: 32px;
    font-weight: 500; font-size: 20px; color: var(--white);
  }
  .contact-list {
    position: absolute; left: 35px; top: 104px;
    list-style: none; font-size: 14px; color: var(--white);
  }
  .contact-list li { display: flex; align-items: center; gap: 9px; height: 19.5px; }
  .contact-list svg { width: 12px; height: 12px; fill: var(--white); }
  .contact-address { margin-top: 6px; }
  .band-mark {
    position: absolute; left: 345px; top: 10px;
    width: 185px; height: 185px; border-radius: 12px;
    background: linear-gradient(135deg, #e4e4e4, var(--silver));
  }
</style>
</head>
<body>
  <section class="card card-front">
    <div class="front-mark"></div>
    <div class="front-wordmark">KVTL</div>
    <div class="front-url">www.agentur-kvtl.de</div>
  </section>

  <section class="card card-back">
    <div class="back-logo">
      <div class="back-logo-square"></div>
      <div class="back-wordmark">KVTL</div>
    </div>
    <div class="contact-band">
      <div class="person-name">VORNAME NAME</div>
      <ul class="contact-list">
        <li><svg viewBox="0 0 24 24"><path d="M6.6 10.8a15 15 0 0 0 6.6 6.6l2.2-2.2c.3-.3.7-.4 1-.2 1.1.4 2.3.6 3.6.6.6 0 1 .4 1 1V20c0 .6-.4 1-1 1A17 17 0 0 1 3 4c0-.6.4-1 1-1h3.5c.6 0 1 .4 1 1 0 1.3.2 2.5.6 3.6.1.3 0 .7-.2 1z"/></svg>07146-839214-0</li>
        <li><svg viewBox="0 0 24 24"><path d="M2 5h20v2l-10 6L2 7z M2 9l10 6 10-6v10H2z"/></svg>Name@agentur-kvtl.de</li>
        <li><svg viewBox="0 0 24 24"><path d="M12 2a10 10 0 1 0 0 20 10 10 0 0 0 0-20zm-1 17.9A8 8 0 0 1 4.1 10H7l2 2v1l2 2zm6.9-2.5A2 2 0 0 0 16 16h-1v-3l-2-1H9V9h2l1-2V5.3a8 8 0 0 1 5.9 12.1z"/></svg>www.agentur-kvtl.de</li>
        <li class="contact-address">Kellberger Str. 18, 73614 Schorndorf</li>
      </ul>
      <div class="band-mark"></div>
    </div>
  </section>
</body>
</html>
```